Car Care labels for Soap,Interior Detailer,Wax,tire shine and All purpose cleaner

Project Overview:
We are launching a premium line of car care products under the GlenVy brand and are looking for a high end, luxurious design for our product labels. The line includes a soap, a wax, an all-purpose cleaner, and an interior detailer. We already have a logo and color palette, and we have some basic bottle shapes picked out. Now we need a refined, eye catching label design that will elevate the look to something that feels upscale and classy, without being overly flashy.

Design Goals:
• Luxurious and Sophisticated: The overall aesthetic should feel premium and elegant. Think clean lines, refined typography, and a color scheme that reflects luxury like deep blacks, rich metallics, or subtle gradients that feel high end.
• Cohesive Branding: Each product label should feel like part of the same family, with a consistent design language across all items.
• Subtle and Tasteful: The design should be elegant but not overly busy. We want it to be eye catching on the shelf but still minimalist and refined.

```html
<!DOCTYPE html>
<html lang="en">
<head>
<meta charset="utf-8">
<title>GlenVy Car Care Labels</title>
<link rel="stylesheet" href="https://fonts.googleapis.com/css2?family=Roboto+Condensed:wght@400;500;700&display=swap">
<style>
  :root {
    --backdrop: #e6e6e6;
    --label-black: #1e1e1e;
    --label-edge: #2a2a2a;
    --gold: #c9ad7c;
    --gold-light: #e4cfa3;
    --gold-dark: #8f7548;
    --photo-dark: #161616;
    --photo-mid: #4a4a4a;
    --pill-text: #1a1a1a;
  }
  * { box-sizing: border-box; margin: 0; padding: 0; }
  html, body {
    width: 1130px;
    height: 1200px;
    overflow: hidden;
    background: var(--backdrop);
    font-family: "Roboto Condensed", Arial, sans-serif;
  }
  .label-set {
    position: relative;
    width: 1130px;
    height: 1200px;
    display: flex;
    justify-content: center;
    align-items: center;
    gap: 70px;
  }
  .label {
    position: relative;
    width: 440px;
    height: 880px;
    background: var(--label-black);
    border: 1px solid var(--label-edge);
    display: flex;
    flex-direction: column;
    align-items: center;
    overflow: hidden;
  }
  .brand {
    margin-top: 70px;
    display: flex;
    flex-direction: column;
    align-items: center;
    color: var(--gold);
  }
  .brand-row {
    display: flex;
    align-items: center;
    gap: 12px;
  }
  .brand-dot {
    width: 18px;
    height: 18px;
    border-radius: 50%;
    background: var(--gold);
  }
  .brand-name {
    font-weight: 700;
    font-size: 64px;
    letter-spacing: 4px;
    line-height: 1;
    color: var(--gold);
  }
  .brand-tagline {
    margin-top: 8px;
    font-weight: 700;
    font-size: 20px;
    letter-spacing: 1px;
    color: var(--gold);
    border: 2px solid var(--gold);
    padding: 2px 12px;
  }
  .product-photo {
    margin-top: 40px;
    width: 100%;
    height: 420px;
    display: block;
  }
  .product-title {
    margin-top: 36px;
    font-weight: 500;
    font-size: 38px;
    letter-spacing: 0.5px;
    color: var(--gold);
    text-align: center;
    line-height: 1;
  }
  .product-subtitle {
    margin-top: 6px;
    font-weight: 400;
    font-size: 22px;
    color: var(--gold);
  }
  .volume-pill {
    margin-top: 18px;
    padding: 6px 22px;
    border-radius: 22px;
    background: linear-gradient(180deg, var(--gold-light), var(--gold) 60%, var(--gold-dark));
    color: var(--pill-text);
    font-weight: 700;
    font-size: 24px;
  }
</style>
</head>
<body>
<main class="label-set">

  <section class="label label--interior">
    <div class="brand">
      <div class="brand-row">
        <span class="brand-dot"></span>
        <span class="brand-name">GlenVy</span>
      </div>
      <span class="brand-tagline">Harborview Auto Care</span>
    </div>
    <svg class="product-photo" viewBox="0 0 440 420" role="img" aria-label="Black and white photo of a car interior dashboard and air vents, overlaid with fine gold wave lines">
      <defs>
        <radialGradient id="interiorTone" cx="55%" cy="45%" r="65%">
          <stop offset="0" stop-color="#5a5a5a"/>
          <stop offset="0.6" stop-color="#2c2c2c"/>
          <stop offset="1" stop-color="#161616"/>
        </radialGradient>
      </defs>
      <rect width="440" height="420" fill="url(#interiorTone)"/>
    </svg>
    <h2 class="product-title">INTERIOR DETAILER</h2>
    <p class="product-subtitle">CLEANER</p>
    <span class="volume-pill">750 ml</span>
  </section>

  <section class="label label--tire">
    <div class="brand">
      <div class="brand-row">
        <span class="brand-dot"></span>
        <span class="brand-name">GlenVy</span>
      </div>
      <span class="brand-tagline">Harborview Auto Care</span>
    </div>
    <svg class="product-photo" viewBox="0 0 440 420" role="img" aria-label="Black and white photo of a car wheel with alloy rim and tire, overlaid with fine gold wave lines">
      <defs>
        <radialGradient id="tireTone" cx="40%" cy="55%" r="60%">
          <stop offset="0" stop-color="#6a6a6a"/>
          <stop offset="0.55" stop-color="#303030"/>
          <stop offset="1" stop-color="#161616"/>
        </radialGradient>
      </defs>
      <rect width="440" height="420" fill="url(#tireTone)"/>
    </svg>
    <h2 class="product-title">TIRE SHINE</h2>
    <span class="volume-pill">750 ml</span>
  </section>

</main>
</body>
</html>
```